Graphic Design Project

We make rose petal jelly from old fashioned english roses. The jelly is sweet eaten with scones and clotted cream or as a filling in a victoria sandwich, as a topping on ice cream or thick set yogurt.
The image of the product is luxurious and decadent and very english.
We need a design for a label which has a picture of an old fashioned rose (rosa mundi or a compte de chambard) The rose must stand out clearly so the jelly is not confused with other fruit jams. The overall colour of the label should be pink and soft, with white or dark pink writing. The label needs to be fridge proof.

We also need a security strip to fit on the lid of the jar.

We need the following information on the label.
Name of our company-"Meadow Crown"
Name of Product-"Rose Petal Jelly"
Sales pitch-"With whole petals-a taste of summer, delicious on scones, as a filling in sponge cake, as a topping on ice cream or yogurt."
INGREDIENTS: Sugar, water, rose petals, lemon juice, natural jelling agent (agar-agar)
STORAGE: Store in a cool dry place, once opened keep refrigerated and consume within 4 weeks.
BEST BEFORE: See base

200g
Produced by:
MEADOW CROWN
The Larches
Pardew Lane
Wrenley
Severnshire
GL17 4RX
The label must have room for a bar code. The size of label approx 8-10cm long 5cm wide.
Updates

Hi

Just been looking at the Hartwell and Brace site and the labels they have there have the up market feel I am trying to convey. Hope that helps, its classy but not twee.

Thanks

Thanks for all submissions. I would be grateful if you googled images for 'Colourful and expensive biscuits at Hartwell Brace' The designs on the tins are the image we are trying to create. The colours are quite strong.

Thanks

Target Market(s)

older well off people who visit garden centres

Industry/Entity Type

Security

Requirements
Must have
• All writen info above and picture of old fashioned rose prferably rose a mundi. Luxury feel, very english, to appeal to older market
Pink colour sheme
Should not have
• dark or manly colours

```html
<!DOCTYPE html>
<html lang="en">
<head>
<meta charset="utf-8">
<title>Meadow Crown Rose Petal Jelly Label</title>
<link rel="stylesheet" href="https://fonts.googleapis.com/css2?family=Cormorant+Garamond:wght@500;600&display=swap">
<style>
  :root {
    --label-magenta: #d5046b;
    --label-white: #ffffff;
    --brand-pink: #f49bd2;
    --soft-pink: #f6addb;
    --info-plum: #8c1350;
    --rose-deep: #b0104f;
    --rose-mid: #c8175f;
    --leaf-green: #6f7a35;
    --barcode-line: #000000;
  }
  * { margin: 0; padding: 0; box-sizing: border-box; }
  html, body { width: 1200px; height: 750px; overflow: hidden; background: var(--label-white); }
  .label {
    position: relative;
    width: 1200px;
    height: 750px;
    font-family: "Cormorant Garamond", "Times New Roman", serif;
    font-weight: 500;
    font-variant-numeric: oldstyle-nums;
  }
  .front-panel {
    position: absolute;
    left: 0; top: 0;
    width: 797px; height: 750px;
    background: var(--label-magenta);
    text-align: center;
  }
  .brand-name {
    position: absolute;
    left: 0; width: 818px; top: 36px;
    font-size: 58px;
    font-weight: 500;
    color: var(--brand-pink);
    line-height: 1;
  }
  .product-name {
    position: absolute;
    left: 0; width: 826px; top: 110px;
    font-size: 80px;
    font-weight: 500;
    color: var(--label-white);
    line-height: 1;
  }
  .tagline {
    position: absolute;
    left: 0; width: 813px; top: 198px;
    font-size: 27px;
    color: var(--soft-pink);
  }
  .rose-art {
    position: absolute;
    left: 272px; top: 288px;
    width: 270px; height: 242px;
  }
  .serving-ideas {
    position: absolute;
    left: 0; width: 828px; top: 578px;
    font-size: 33px;
    line-height: 41px;
    color: var(--soft-pink);
  }
  .net-weight {
    position: absolute;
    left: 610px; top: 700px;
    font-size: 34px;
    color: var(--label-white);
    line-height: 1;
  }
  .info-panel {
    position: absolute;
    left: 818px; top: 26px;
    width: 380px;
    color: var(--info-plum);
    font-size: 23.5px;
    line-height: 30px;
  }
  .info-block { position: absolute; left: 0; white-space: nowrap; }
  .info-ingredients { top: 0; }
  .info-storage { top: 124px; }
  .info-best-before { top: 251px; }
  .producer {
    position: absolute;
    left: 818px; top: 378px;
    color: var(--info-plum);
    font-size: 30px;
    line-height: 35px;
    font-style: normal;
  }
  .barcode-space {
    position: absolute;
    left: 1001px; top: 636px;
    width: 176px; height: 90px;
    border: 1px solid var(--barcode-line);
    font-family: Arial, Helvetica, sans-serif;
    font-size: 18px;
    line-height: 22px;
    padding: 21px 0 0 8px;
    font-variant-numeric: normal;
  }
</style>
</head>
<body>
<main class="label">
  <section class="front-panel">
    <h2 class="brand-name">Meadow Crown</h2>
    <h1 class="product-name">Rose Petal Jelly</h1>
    <p class="tagline">"With whole petals its a taste of summer”</p>
    <svg class="rose-art" viewBox="0 0 270 242" role="img" aria-label="Illustration of an old fashioned crimson rose with buds and green leaves">
      <defs>
        <radialGradient id="roseBloom" cx="45%" cy="45%" r="60%">
          <stop offset="0%" stop-color="var(--rose-mid)"/>
          <stop offset="60%" stop-color="var(--rose-deep)"/>
          <stop offset="100%" stop-color="var(--leaf-green)" stop-opacity="0.85"/>
        </radialGradient>
      </defs>
      <rect width="270" height="242" rx="110" fill="url(#roseBloom)"/>
    </svg>
    <p class="serving-ideas">Delicious on scones, as a filling<br>in sponge cake, as a topping<br>on ice cream or yogurt.</p>
    <p class="net-weight">200g</p>
  </section>

  <section class="info-panel">
    <p class="info-block info-ingredients">INGREDIENTS:<br>Sugar, water, rose petals, lemon<br>juice, natural jelling agent (agar-agar)</p>
    <p class="info-block info-storage">STORAGE: Store in a cool dry<br>place, once opened keep refrigerated<br>and consume within 4 weeks.</p>
    <p class="info-block info-best-before">BEST BEFORE:<br>See base</p>
  </section>

  <address class="producer">
    Produced by:<br>
    MEADOW CROWN<br>
    The Larches<br>
    Pardew Lane<br>
    Wrenley<br>
    Severnshire<br>
    GL17 4RX
  </address>

  <div class="barcode-space">Bar<br>Code</div>
</main>
</body>
</html>
```